Real Estate Business Card Design

I'm a Realtor in Vancouver, BC. There are 10,000+ other Realtors in Vancouver, so I need a business card that distinguishes me from the others, something edgy yet classy. The card will be the basis for most of my future marketing efforts and will act as the foundation for branding/marketing, to include; feature sheets, postcards, letterhead and other print material.

I specialize in both detached houses and townhomes/condos.

I've attached files for previous business card. I've also attached a more recent photo to be used on the card.
Updates

New logos and previous designs have been uploaded.  The previous logo was incorrect.

Target Market(s)

Home Buyers and Sellers. Age range is 18-52, newlyweds and/or young families.

Industry/Entity Type

Marketing

Requirements
Must have
• 2 sided business card with all appropriate information. I won't be using my last name as part of the title since I find people are more curious about my ethnicity than that I'm a Realtor.

Website will be: agentmilo.com
email: milo@agentmilo.com
I'll be using "Realtor Milo" as the title name.

Social Medial Links similar to existing card.
Nice to have
• Would like to see my existing card with the updated picture of myself and the "condos" in the background replaced/removed.

```html
<!DOCTYPE html>
<html lang="en">
<head>
<meta charset="utf-8">
<title>Realtor Milo – Business Card</title>
<link rel="stylesheet" href="https://fonts.googleapis.com/css2?family=Arimo:wght@400;700&family=Tinos:ital,wght@1,700&display=swap">
<style>
  :root {
    --navy: #0f2d63;
    --white: #ffffff;
    --paper: #ececec;
    --edge-shadow: #5a4a42;
    --photo-light: #d9d9d9;
    --photo-dark: #4a4a4c;
    --sans: "Arimo", Arial, sans-serif;
    --serif: "Tinos", "Times New Roman", serif;
  }
  * { margin: 0; padding: 0; box-sizing: border-box; }
  html, body {
    width: 1162px; height: 1200px; overflow: hidden;
    background: var(--paper);
  }
  .stage { position: relative; width: 1162px; height: 1200px; }
  .card {
    position: absolute; top: 200px;
    width: 460px; height: 800px;
    border-radius: 36px; overflow: hidden;
    box-shadow: 0 6px 18px rgba(0,0,0,.25);
  }
  /* Back side */
  .card-back {
    left: 80px; background: var(--navy); color: var(--white);
    font-family: var(--sans);
  }
  .brand {
    position: absolute; left: 0; right: 0; top: 500px;
    display: flex; flex-direction: column; align-items: center;
  }
  .brand-square {
    width: 14px; height: 14px; background: var(--white); margin-bottom: 10px;
  }
  .brand-name {
    font-family: var(--sans); font-weight: 700; font-size: 24px;
    line-height: 1.05; text-align: center; letter-spacing: .5px;
    color: var(--white);
  }
  .contact-list {
    position: absolute; left: 100px; top: 612px;
    list-style: none; font-size: 17px; line-height: 22px;
  }
  .contact-list li { display: flex; gap: 10px; margin-bottom: 8px; }
  .contact-list svg { flex: none; margin-top: 3px; }
  .social-links { display: flex; gap: 8px; align-items: center; }
  .social-dot {
    width: 16px; height: 16px; border-radius: 50%; background: var(--white);
  }
  /* Front side */
  .card-front { left: 620px; background: var(--white); }
  .card-front svg.face-art { position: absolute; inset: 0; }
  .agent-name { font-family: var(--serif); font-style: italic; font-weight: 700; }
  .agent-title, .phone-number, .vertical-url { font-family: var(--sans); }
</style>
</head>
<body>
<div class="stage">

  <section class="card card-back" aria-label="Card back">
    <div class="brand">
      <div class="brand-square"></div>
      <div class="brand-name">HARBOURLINE<br>REALTY</div>
    </div>
    <ul class="contact-list">
      <li>
        <svg width="16" height="16" viewBox="0 0 16 16" fill="none" stroke="#fff" stroke-width="1.6"><path d="M2 8 L8 2 L14 8"/><path d="M4 7 V14 H12 V7"/><path d="M7 14 V10 H9 V14"/></svg>
        <span>Westside Office<br>1480 Cedar Lane<br>Vancouver, BC V6X 2K4</span>
      </li>
      <li>
        <svg width="16" height="16" viewBox="0 0 16 16" fill="none" stroke="#fff" stroke-width="1.6"><rect x="1.5" y="3.5" width="13" height="9"/><path d="M1.5 3.5 L8 9 L14.5 3.5"/></svg>
        <span>milo@agentmilo.com</span>
      </li>
      <li>
        <svg width="16" height="16" viewBox="0 0 16 16" fill="none" stroke="#fff" stroke-width="1.5"><circle cx="8" cy="8" r="6.5"/><ellipse cx="8" cy="8" rx="2.8" ry="6.5"/><path d="M1.5 8 H14.5"/></svg>
        <span>www.agentmilo.com</span>
      </li>
      <li class="social-links" aria-label="Social media">
        <span class="social-dot" aria-hidden="true"></span>
        <span>@agentmilo</span>
      </li>
    </ul>
  </section>

  <section class="card card-front" aria-label="Card front">
    <svg class="face-art" width="460" height="800" viewBox="0 0 460 800">
      <defs>
        <linearGradient id="photoTone" x1="0" y1="0" x2="0" y2="1">
          <stop offset="0" stop-color="#d9d9d9"/>
          <stop offset="1" stop-color="#4a4a4c"/>
        </linearGradient>
      </defs>
      <rect class="portrait" x="90" y="260" width="300" height="540" fill="url(#photoTone)" role="img" aria-label="Portrait photo of the agent seated, in a dark sweater"/>
      <path class="side-band-shadow" d="M372,260 C412,440 322,570 368,800 L380,800 C334,570 424,440 384,260 Z" fill="var(--edge-shadow)"/>
      <path class="side-band" d="M384,260 C424,440 334,570 380,800 L460,800 L460,260 Z" fill="var(--navy)"/>
      <path class="header-shadow" d="M0,0 H460 V308 Q420,318 380,308 Q340,328 300,313 Q250,338 200,318 Q150,348 100,328 Q50,353 0,338 Z" fill="var(--edge-shadow)"/>
      <path class="header" d="M0,0 H460 V300 Q420,310 380,300 Q340,320 300,305 Q250,330 200,310 Q150,340 100,320 Q50,345 0,330 Z" fill="var(--navy)"/>
      <path class="notch" d="M460,140 L416,162 L460,184 Z" fill="var(--white)"/>

      <text class="agent-name" x="250" y="110" text-anchor="middle" font-size="24" fill="#fff">Realtor Milo</text>
      <text class="agent-title" x="250" y="138" text-anchor="middle" font-size="19" fill="#fff">Real Estate Advisor</text>

      <g class="phone-list" fill="#fff">
        <circle cx="172" cy="186" r="7" fill="none" stroke="#fff" stroke-width="2"/>
        <text class="phone-number" x="200" y="193" font-size="18">604.555.0142</text>
        <rect x="165" y="206" width="14" height="10" rx="2"/>
        <rect x="168" y="202" width="8" height="5" fill="none" stroke="#fff" stroke-width="1.5"/>
        <text class="phone-number" x="200" y="217" font-size="18">604.555.0187</text>
        <rect x="167" y="225" width="9" height="15" rx="2"/>
        <text class="phone-number" x="200" y="241" font-size="18">604.555.0163</text>
      </g>

      <text class="vertical-url" transform="translate(40,700) rotate(-90)" font-size="20" fill="var(--navy)">www.agentmilo.com</text>
      <path class="url-arrow" d="M32,745 L32,732 L26,732 L34,722 L42,732 L36,732 L36,745 Z" fill="var(--navy)"/>
    </svg>
  </section>

</div>
</body>
</html>
```